Looking for a modern, Professional business card design

We have a simple business card, but are looking for a more modern, professional look. A sample of the basic card is attached as well as the logo. We would also like to add that we offer:
Struggling with your finances?
- Learn to become debt free
- Discover the power of cash
- Control your money instead of it controlling you
Let us help you achieve a new level of financial freedom!
Also, we would like to have a "SPECIAL OFFER!: FREE 30 minute consultation"
Financial Planning

```html
<!DOCTYPE html>
<html lang="en">
<head>
<meta charset="utf-8">
<title>Clearpath Money Coaching – Business Card</title>
<link rel="stylesheet" href="https://fonts.googleapis.com/css2?family=Open+Sans:wght@400;600;700&display=swap">
<style>
  :root {
    --backdrop: #161616;
    --card-white: #f3f3f3;
    --ink: #1a1a1a;
    --brand-green: #3a9a2e;
    --lime: #9ccc3a;
    --field-dark: #2a6f22;
    --field-mid: #3d8a2f;
    --text-light: #ffffff;
    --offer: #eaf3b8;
  }
  * { box-sizing: border-box; margin: 0; padding: 0; }
  html, body { width: 1200px; height: 900px; overflow: hidden; }
  body {
    background: var(--backdrop);
    font-family: "Open Sans", Arial, sans-serif;
    position: relative;
  }
  .card {
    position: absolute;
    top: 184px;
    width: 301px;
    height: 490px;
    border-radius: 14px;
    overflow: hidden;
    text-align: center;
  }
  .card-front { left: 299px; background: var(--card-white); color: var(--ink); }
  .card-back { left: 645px; color: var(--text-light); }

  .brand {
    position: absolute;
    left: 0; right: 0;
    display: flex;
    align-items: center;
    justify-content: center;
    gap: 8px;
    font-weight: 700;
    color: var(--brand-green);
  }
  .brand-dot { border-radius: 50%; background: var(--lime); flex: none; }
  .card-front .brand { top: 318px; top: 134px; font-size: 19px; }
  .card-front .brand-dot { width: 22px; height: 22px; }

  .holder { position: absolute; top: 274px; left: 0; right: 0; }
  .holder-name { font-size: 16px; font-weight: 600; line-height: 20px; }
  .holder-role { font-size: 13px; line-height: 18px; }

  .contact { position: absolute; top: 332px; left: 0; right: 0; font-size: 13.5px; line-height: 18px; }

  .back-field {
    position: absolute; inset: 0;
    background: radial-gradient(ellipse at 50% 40%, var(--field-mid) 0%, var(--field-dark) 80%);
  }
  .card-back .brand { top: 78px; font-size: 17px; color: var(--lime); }
  .card-back .brand-dot { width: 26px; height: 26px; }

  .pitch-title { position: absolute; top: 210px; left: 0; right: 0; font-size: 14.5px; font-weight: 700; }
  .benefits {
    position: absolute; top: 254px; left: 58px; right: 40px;
    list-style: none; text-align: left; font-size: 13.5px; line-height: 18px;
  }
  .benefits li { position: relative; padding-left: 20px; }
  .benefits li::before {
    content: ""; position: absolute; left: 2px; top: 5px;
    border-left: 9px solid var(--text-light);
    border-top: 4px solid transparent; border-bottom: 4px solid transparent;
  }
  .benefits .wrap { padding-left: 40px; }
  .invite { position: absolute; top: 340px; left: 0; right: 0; font-size: 13.5px; line-height: 18px; }
  .offer {
    position: absolute; top: 406px; left: 0; right: 0;
    font-size: 16px; font-weight: 700; line-height: 22px; color: var(--offer);
  }
</style>
</head>
<body>
  <section class="card card-front" aria-label="Card front">
    <div class="brand"><span class="brand-dot"></span>Clearpath Money Coaching</div>
    <div class="holder">
      <p class="holder-name">Daniel R. Hayes</p>
      <p class="holder-role">Personal financial coach</p>
    </div>
    <div class="contact">
      <p>(555) 014-2298</p>
      <p>daniel@clearpathmoneycoach.com</p>
      <p>www.clearpathmoneycoach.com</p>
    </div>
  </section>

  <section class="card card-back" aria-label="Card back">
    <div class="back-field" role="img" aria-label="Green field with a repeating pattern of the brand symbol"></div>
    <div class="brand"><span class="brand-dot"></span>Clearpath</div>
    <h2 class="pitch-title">Struggling with your finances?</h2>
    <ul class="benefits">
      <li>Learn to become debt free</li>
      <li>Discover the power of cash</li>
      <li>Control your money instead</li>
      <li class="wrap" style="list-style:none">of it controlling you</li>
    </ul>
    <p class="invite">Let us help you achieve a new level<br>of financial freedom!</p>
    <p class="offer">SPECIAL OFFER!<br>FREE 30 MINUTE CONSULTATION</p>
  </section>
</body>
</html>
```